Business Card for premium dental clinic

We are a premium dental clinic based in Brasov, Romania with more than 15 year on the market, providing quality dental treatment made by a team of more specialized dentists, working with modern equipment as a solution to beautiful and healthy teeth.

Our current logo for the clinic use 2 square with colors black and gold - dr Ternisu - studio, using family fonts Bodoni, Myriad Pro and Segoe Print.
Depending on the printing we used some gold CMYK background or gold foil picture background or a gold gradient.
We want a business card:
- eye catching business card
- distinguished business card
- premium design
- to keep the color scheme of black and gold
- to attract the customers to spent time reading the information
- modern concept

```html
<!DOCTYPE html>
<html lang="en">
<head>
<meta charset="utf-8">
<title>Ternisu Clinic – Business Card</title>
<link rel="stylesheet" href="https://fonts.googleapis.com/css2?family=Montserrat:wght@400;500;700&display=swap">
<style>
  :root {
    --canvas: #2b2623;
    --card: #303032;
    --gold: #d2a93c;
    --gold-light: #f6df7c;
    --gold-dark: #a97a1c;
    --white: #ffffff;
    --muted-gold: #c79d3a;
  }
  * { margin: 0; padding: 0; box-sizing: border-box; }
  html, body {
    width: 1200px; height: 800px; overflow: hidden;
    background: var(--canvas);
    font-family: "Montserrat", sans-serif;
  }
  .stage {
    position: relative; width: 1200px; height: 800px;
    display: flex; align-items: center; justify-content: center; gap: 40px;
  }
  .card {
    position: relative; width: 530px; height: 303px;
    background: var(--card);
    overflow: hidden;
    box-shadow: 0 10px 30px rgba(0,0,0,.45);
  }
  .card--front { display: flex; align-items: center; justify-content: center; }
  .brand-name {
    font-family: "Montserrat", sans-serif;
    font-weight: 500; color: var(--gold);
    letter-spacing: 1px; white-space: nowrap;
  }
  .card--front .brand-name { font-size: 46px; }

  .holder { position: absolute; left: 40px; top: 66px; }
  .holder__name { color: var(--white); font-weight: 700; font-size: 20px; letter-spacing: .3px; }
  .holder__role { color: var(--muted-gold); font-size: 10px; margin-top: 1px; }
  .rule { position: absolute; height: 1px; background: var(--gold); }
  .rule--top { left: 40px; right: 40px; top: 116px; }
  .rule--bottom { left: 330px; right: 40px; top: 208px; }
  .contacts { position: absolute; left: 40px; top: 128px; list-style: none; }
  .contacts li {
    display: flex; align-items: center; gap: 10px;
    color: var(--gold); font-size: 11.5px; height: 19px;
  }
  .contacts svg { width: 11px; height: 11px; fill: var(--white); flex: none; }
  .card--back .brand-name {
    position: absolute; right: 40px; top: 148px; font-size: 28px;
  }
  .address {
    position: absolute; right: 40px; top: 220px;
    color: var(--gold); font-size: 12px; line-height: 1.35; text-align: right;
  }
  .wave { position: absolute; inset: 0; width: 100%; height: 100%; }
</style>
</head>
<body>
<main class="stage">
  <section class="card card--front" aria-label="Card front">
    <span class="brand-name">Ternisu Clinic</span>
  </section>

  <section class="card card--back" aria-label="Card back">
    <svg class="wave" viewBox="0 0 530 303" preserveAspectRatio="none" aria-hidden="true">
      <defs>
        <linearGradient id="goldBand" x1="0" y1="0" x2="1" y2="0">
          <stop offset="0" stop-color="var(--gold-dark)"/>
          <stop offset=".35" stop-color="var(--gold-light)"/>
          <stop offset=".7" stop-color="var(--gold)"/>
          <stop offset="1" stop-color="var(--gold-dark)"/>
        </linearGradient>
      </defs>
      <path d="M0,206 C120,198 230,256 340,274 C420,286 480,286 530,282 L530,303 L0,303 Z" fill="var(--white)"/>
      <path d="M0,215 C130,209 230,263 340,281 C420,293 480,293 530,291 L530,303 L0,303 Z" fill="url(#goldBand)"/>
    </svg>

    <div class="holder">
      <p class="holder__name">Mara Ilie</p>
      <p class="holder__role">Manager</p>
    </div>
    <div class="rule rule--top"></div>

    <ul class="contacts">
      <li>
        <svg viewBox="0 0 24 24"><path d="M6.6 10.8a15.1 15.1 0 0 0 6.6 6.6l2.2-2.2a1 1 0 0 1 1-.25 11.4 11.4 0 0 0 3.6.57 1 1 0 0 1 1 1V20a1 1 0 0 1-1 1A17 17 0 0 1 3 4a1 1 0 0 1 1-1h3.5a1 1 0 0 1 1 1c0 1.25.2 2.450.57 3.57a1 1 0 0 1-.25 1z"/></svg>
        0268-555-014
      </li>
      <li>
        <svg viewBox="0 0 24 24"><path d="M2 5h20v14H2z M4 7v.4l8 5 8-5V7l-8 5z" fill-rule="evenodd"/></svg>
        office@ternisu.ro
      </li>
      <li>
        <svg viewBox="0 0 24 24"><path d="M12 2a10 10 0 1 0 0 20 10 10 0 0 0 0-20zm0 2c.9 1.2 1.6 2.6 2 4h-4c.4-1.4 1.1-2.8 2-4zM4.3 14a8 8 0 0 1 0-4h3.4a16 16 0 0 0 0 4zm.8 2h3a15 15 0 0 0 1.4 3.6A8 8 0 0 1 5.1 16zm3-8h-3a8 8 0 0 1 4.4-3.6A15 15 0 0 0 8.1 8zM12 20c-.9-1.2-1.6-2.6-2-4h4c-.4 1.4-1.1 2.8-2 4zm2.3-6H9.7a14 14 0 0 1 0-4h4.6a14 14 0 0 1 0 4zm.2 5.6A15 15 0 0 0 15.9 16h3a8 8 0 0 1-4.4 3.6zM16.3 14a16 16 0 0 0 0-4h3.4a8 8 0 0 1 0 4zm-.4-6a15 15 0 0 0-1.4-3.6A8 8 0 0 1 18.9 8z"/></svg>
        www.ternisu-clinic.ro
      </li>
    </ul>

    <span class="brand-name">Ternisu Clinic</span>
    <div class="rule rule--bottom"></div>
    <p class="address">Your address, city<br>state, ZIP 0000</p>
  </section>
</main>
</body>
</html>
```